Vantiqo custom business card design

Need a authentic, innovative business card design for a new mobile app business. I am uploading a few screen images from our app for you to view. I would like app design theme to match business card design. I can also send logo images.

```html
<!DOCTYPE html>
<html lang="en">
<head>
<meta charset="utf-8">
<title>Vantiqo Business Card</title>
<link rel="stylesheet" href="https://fonts.googleapis.com/css2?family=Montserrat:wght@700&family=Open+Sans:wght@400;600&display=swap">
<style>
  :root {
    --backdrop: #3b3431;
    --card: #141214;
    --purple: #7a14b8;
    --purple-soft: #8d2fd0;
    --silver: #d9d9d9;
    --text-light: #cfcfcf;
    --divider: #3a3a3a;
  }
  * { box-sizing: border-box; margin: 0; padding: 0; }
  html, body {
    width: 1200px; height: 844px; overflow: hidden;
    background: var(--backdrop);
  }
  .stage {
    position: relative; width: 1200px; height: 844px;
    display: flex; align-items: center; justify-content: center; gap: 50px;
  }
  .card {
    width: 510px; height: 292px;
    background: var(--card);
    box-shadow: 0 14px 30px rgba(0,0,0,.45);
    position: relative;
  }
  /* contact side */
  .card-back { display: flex; align-items: center; }
  .brand-block {
    width: 200px; height: 100%;
    display: flex; align-items: center; justify-content: center; gap: 10px;
  }
  .brand-dot {
    width: 30px; height: 30px; border-radius: 50%;
    background: var(--purple);
  }
  .brand-name {
    font-family: "Montserrat", sans-serif; font-weight: 700;
    font-size: 28px; color: var(--purple-soft);
  }
  .divider {
    width: 1px; height: 150px; background: var(--divider);
  }
  .contact {
    padding-left: 22px;
    font-family: "Open Sans", sans-serif; color: var(--text-light);
    font-size: 14px; line-height: 19px;
  }
  .contact-name {
    font-family: "Montserrat", sans-serif; font-weight: 700;
    color: var(--purple-soft); font-size: 18px; letter-spacing: .5px;
    line-height: 20px;
  }
  .contact-role { margin-bottom: 2px; }
  .contact-row { display: flex; align-items: center; gap: 8px; }
  .contact-row svg { width: 11px; height: 11px; flex: none; fill: var(--purple-soft); }
  .contact-address { margin-top: 8px; }
  /* logo side */
  .card-front {
    display: flex; align-items: center; justify-content: center; gap: 14px;
  }
  .front-dot {
    width: 44px; height: 44px; border-radius: 50%;
    background: var(--silver);
  }
  .front-name {
    font-family: "Montserrat", sans-serif; font-weight: 700;
    font-size: 42px; color: var(--silver);
  }
</style>
</head>
<body>
<main class="stage">
  <section class="card card-back" aria-label="Contact side">
    <div class="brand-block">
      <span class="brand-dot"></span>
      <span class="brand-name">Vantiqo</span>
    </div>
    <div class="divider"></div>
    <div class="contact">
      <p class="contact-name">MARCUS ELLERY</p>
      <p class="contact-role">Managing Director</p>
      <p class="contact-row">
        <svg viewBox="0 0 12 12"><path d="M2 1h3l1 3-1.5 1a6 6 0 0 0 2.5 2.5L8 6l3 1v3c0 .6-.4 1-1 1A9 9 0 0 1 1 2c0-.6.4-1 1-1z"/></svg>
        044-987 650 412</p>
      <p class="contact-row">
        <svg viewBox="0 0 12 12"><path d="M3 0h6a1 1 0 0 1 1 1v10a1 1 0 0 1-1 1H3a1 1 0 0 1-1-1V1a1 1 0 0 1 1-1zm0 2v7h6V2z"/></svg>
        044-987 650 413</p>
      <p class="contact-row">
        <svg viewBox="0 0 12 12"><path d="M0 2h12v8H0zm1 1v.5l5 3 5-3V3z"/></svg>
        hello@vantiqo.com</p>
      <p class="contact-row">
        <svg viewBox="0 0 12 12"><circle cx="6" cy="6" r="6"/></svg>
        www.vantiqo.com</p>
      <p class="contact-address">48 Harbour Lane, Northfield<br>Westmoor, 204170.</p>
    </div>
  </section>

  <section class="card card-front" aria-label="Logo side">
    <span class="front-dot"></span>
    <span class="front-name">Vantiqo</span>
  </section>
</main>
</body>
</html>
```